Exclusive beauty salon needs a price list or services booklet

I need a new very attractive flyer for my beauty salon, containing information on the different services and their prices.
In attachment you can find a pdf of the "old" one, but I'd love to have a beautifully designed new one!
I'd love to have a booklet in format 148 x 148 mm, or in US format, containing 12 or 16 pages, but if you can offer other nice looking designs they are welcome!
The services that need to come in the booklet with their prices can all be found on my website: www.atelierverano.be, starting with
Gelaatsverzorging
Wimperverlenging
Suikerontharing
Wimperlifting
Permanente Make Up
Airbrush Tanning

Target Market(s)

woman from 20 to 89 years old

Industry/Entity Type

Beauty Salon

Font styles to use
Sans Serif

Colors

Designer to choose colors to be used in the design.

Requirements
Must have
• a classy nice look, it must contain details about the services from my beauty salon and their prices, and nice pictures.
• The Names, prices and explanations of the services can easily be found on my website: www.atelierverano.be
Nice to have
• In attachment you can find the "old" price list in pdf, what I need now is a "new booklet" with the new logo and updated services price list.
• I need a very nice and attractive looking booklet, classy chique, Paris chique, looking very expensive.
Should not have
• Not too much colors, not too curly, but still feminine

```html
<!DOCTYPE html>
<html lang="nl">
<head>
<meta charset="utf-8">
<title>Ontharing Met Suiker – Verano</title>
<link rel="stylesheet" href="https://fonts.googleapis.com/css2?family=Open+Sans:ital,wght@0,400;1,400&display=swap">
<style>
  :root {
    --frame: #a7a9ab;
    --card: #ffffff;
    --accent: #3fb6c6;
    --text: #8b8c8e;
  }
  * { box-sizing: border-box; margin: 0; padding: 0; }
  html, body { width: 1200px; height: 868px; overflow: hidden; background: var(--frame); }
  .page {
    position: relative;
    width: 1200px;
    height: 868px;
    background: var(--frame);
    font-family: "Open Sans", Arial, sans-serif;
  }
  .card {
    position: absolute;
    left: 34px; top: 34px;
    width: 1132px; height: 800px;
    background: var(--card);
    display: flex;
  }
  .hero-photo {
    width: 545px;
    height: 100%;
    flex-shrink: 0;
    background: linear-gradient(200deg,
      #fbfaf9 0%,
      #f6ece6 12%,
      #e7b99c 24%,
      #e3a064 33%,
      #d99877 42%,
      #c98a6c 55%,
      #b97a5e 66%,
      #d7b4a0 76%,
      #efe9e6 84%,
      #f7f3f1 92%,
      #e9d7d3 100%);
  }
  .content {
    padding: 50px 0 0 52px;
    flex: 1;
    color: var(--text);
  }
  .title {
    font-weight: 400;
    font-size: 25px;
    line-height: 30px;
    color: var(--accent);
    margin-bottom: 16px;
  }
  .intro, .lead, .benefit {
    font-style: italic;
    font-weight: 400;
    font-size: 18px;
    line-height: 25px;
    white-space: nowrap;
  }
  .intro { margin-bottom: 8px; }
  .lead { margin-bottom: 19px; }
  .benefits { list-style: none; }
  .benefit {
    position: relative;
    padding-left: 22px;
    margin-bottom: 8px;
  }
  .benefit svg {
    position: absolute;
    left: 2px; top: 9px;
    width: 12px; height: 10px;
  }
</style>
</head>
<body>
<div class="page">
  <div class="card">
    <div class="hero-photo" role="img" aria-label="Foto van een been waarop een strook suikerpasta wordt aangebracht, rustend op een witte handdoek met rozenblaadjes"></div>
    <div class="content">
      <h1 class="title">Ontharing Met Suiker</h1>
      <p class="intro">Heb je ook genoeg van lichaams- en/of gezichtsbeharing<br>maar ben je niet tevreden met het resultaat van<br>scheren/harsen/laseren? Dan is ontharen met suiker van<br>Verano dé oplossing!</p>
      <p class="lead">De voordelen van ontharen met suiker:</p>
      <ul class="benefits">
        <li class="benefit"><svg viewBox="0 0 12 10"><path d="M1 5.5 L4.5 8.5 L11 1.5" fill="none" stroke="var(--accent)" stroke-width="1.8"/></svg>De haren worden met de haargroeirichting verwijderd,<br>hierdoor vermindert de pijn en je hebt geen last van<br>haartjes die afbreken</li>
        <li class="benefit"><svg viewBox="0 0 12 10"><path d="M1 5.5 L4.5 8.5 L11 1.5" fill="none" stroke="var(--accent)" stroke-width="1.8"/></svg>De haren worden volledig verwijderd (met de haarwortel)<br>waardoor ze dunner en donziger worden en minder snel<br>aangroeien</li>
        <li class="benefit"><svg viewBox="0 0 12 10"><path d="M1 5.5 L4.5 8.5 L11 1.5" fill="none" stroke="var(--accent)" stroke-width="1.8"/></svg>Er wordt hygiënisch gewerkt</li>
        <li class="benefit"><svg viewBox="0 0 12 10"><path d="M1 5.5 L4.5 8.5 L11 1.5" fill="none" stroke="var(--accent)" stroke-width="1.8"/></svg>De huidstructuur verbetert door het verwijderen van dode<br>huidcellen zonder de levende cellen te beschadigen</li>
        <li class="benefit"><svg viewBox="0 0 12 10"><path d="M1 5.5 L4.5 8.5 L11 1.5" fill="none" stroke="var(--accent)" stroke-width="1.8"/></svg>Suiker bestaat uit lichaamseigen stoffen waardoor de huid<br>minder fel reageert op de ontharing.</li>
        <li class="benefit"><svg viewBox="0 0 12 10"><path d="M1 5.5 L4.5 8.5 L11 1.5" fill="none" stroke="var(--accent)" stroke-width="1.8"/></svg>Suikerontharing zorgt ervoor dat de haargroei vermindert<br>na iedere behandeling en verfijnt de haarstructuur</li>
        <li class="benefit"><svg viewBox="0 0 12 10"><path d="M1 5.5 L4.5 8.5 L11 1.5" fill="none" stroke="var(--accent)" stroke-width="1.8"/></svg>Met suikerontharing werkt men op lichaamstemperatuur<br>dus geen brandwonden</li>
        <li class="benefit"><svg viewBox="0 0 12 10"><path d="M1 5.5 L4.5 8.5 L11 1.5" fill="none" stroke="var(--accent)" stroke-width="1.8"/></svg>Suikerontharing is geschikt voor de couperose huid en is uiterst<br>geschikt voor de meest gevoelige plaatsen (bikini, gezicht,...)</li>
        <li class="benefit"><svg viewBox="0 0 12 10"><path d="M1 5.5 L4.5 8.5 L11 1.5" fill="none" stroke="var(--accent)" stroke-width="1.8"/></svg>Suiker is wateroplosbaar, dus geen ongewenste plakseltjes</li>
      </ul>
    </div>
  </div>
</div>
</body>
</html>
```